Corbeck Aluminium Design Upgrade

- This is for a layout design of the home page only. No coding required.

- The design should be based around the attached HPID (home page information design) I've attached both a JPEG of this
- Information only is in RED text. Copy to go on the design in BLACK text. Some instructions are in the HPID. Please be creative!
- The design needs to be clean and spacious
- Use the logo provided. Please use the colours from the logos in the website design.
- I've attached some images to use as examples to use for home page gallery
- The product logos (Pelvane, Trimbough etc) showed in the HPV can be googled for a higher quality image if required.
- The header can be changed/altered - just needs to have all information as per logo, along with the phone number.

- Expected standard of design examples: (Please DO NOT copy these exactly – they are just examples)
http://www.halden-works.example.nz/
http://www.plinthcove.example.nz/
http://www.dusofern.example.nz/

Width of content will be 1100 pixels when implemented as a web page. Header height (without nav bar) 150-160 pixels.

The winning PSD file will have to be provided as follows…
1. Canvas size of 2000px x 2000px - 72ppi in Adobe Photoshop (CS5 compatible)
2. Width of content section is 1100px wide - centered in the canvas
3. Any button rollovers/hovers in the PSD as hidden layers.
4. All fonts used must be Google fonts (except for the header fonts).
5. You will need to supply the chosen home page plus one example page (example page as a style guide for how all other pages will look). Example page is only the header and navigational bar at the top, an empty sector in the middle with a column (180 px wide) which can be left or right aligned which means the main sector is 920 pixels wide, and then the footer at the bottom of the page.

```html
<!DOCTYPE html>
<html lang="en">
<head>
<meta charset="utf-8">
<title>Corbeck Aluminium Ltd</title>
<link rel="stylesheet" href="https://fonts.googleapis.com/css2?family=Open+Sans:ital,wght@0,400;0,600;0,700;1,400&family=Arimo:ital,wght@0,400;0,700;1,400&display=swap">
<style>
:root{
  --navy:#0b1c86;
  --navy-deep:#0a1878;
  --red:#e3141b;
  --yellow:#fff200;
  --nav-bg:#f1f1f1;
  --ink:#333;
  --muted:#8a8a8a;
  --card-head:#3d3d3d;
  --card-body:#e8eef5;
  --link:#0a2a8a;
  --rule:#e2e2e2;
  --gold:#c99a1e;
}
*{box-sizing:border-box;margin:0;padding:0}
html,body{width:1200px;height:2206px;overflow:hidden;background:#fff}
body{position:relative;font-family:"Arimo",Arial,sans-serif;color:var(--ink)}
.abs{position:absolute}

/* header */
.site-header{position:absolute;left:0;top:0;width:1200px;height:150px;background:var(--navy)}
.brand{position:absolute;left:85px;top:24px;color:#fff;font-family:"Open Sans",sans-serif;font-weight:700;line-height:1}
.brand-name{font-size:50px;letter-spacing:-1px}
.brand-sub{font-size:32px;margin-top:4px;padding-left:32px}
.brand-place{font-size:12px;margin-top:6px;padding-left:104px;letter-spacing:1px}
.brand-square{position:absolute;left:385px;top:22px;width:91px;height:104px;background:var(--red)}
.call{position:absolute;left:716px;top:46px;color:#fff;font-family:"Open Sans",sans-serif;font-size:20px}
.excellence{position:absolute;left:500px;top:107px;height:19px;width:431px;display:flex;font-family:"Open Sans",sans-serif;font-size:13px;font-weight:700;letter-spacing:1px}
.excellence .lead{background:var(--yellow);color:#111;padding:0 14px;font-style:italic;line-height:19px}
.excellence .rest{background:var(--red);color:#fff;flex:1;padding-left:10px;line-height:19px;font-weight:400}
.partner-mark{position:absolute;left:948px;top:30px;display:flex;align-items:center;gap:10px;color:#fff;font-family:"Open Sans",sans-serif;font-size:22px;font-weight:700;letter-spacing:3px}
.partner-mark i{display:block;width:26px;height:26px;background:var(--red)}

/* nav */
.main-nav{position:absolute;left:0;top:150px;width:1200px;height:65px;background:var(--nav-bg);border-bottom:1px solid #dcdcdc;display:flex;justify-content:space-between;align-items:center;padding:0 99px 0 97px}
.main-nav a{font-family:"Open Sans",sans-serif;font-size:12px;color:#555;text-decoration:none;text-transform:uppercase}
.tagline{position:absolute;left:0;top:215px;width:1200px;height:59px;text-align:center;line-height:59px;font-family:"Open Sans",sans-serif;font-weight:600;font-size:19px;color:#333;letter-spacing:.3px}

/* hero */
.hero{position:absolute;left:0;top:274px;width:1200px;height:507px;overflow:hidden}
.hero-photo{position:absolute;inset:0;background:linear-gradient(180deg,#8fb6e0 0%,#c9def2 22%,#e9e9e6 45%,#d5d3cf 62%,#6b7a4a 80%,#4a5d35 100%)}
.hero-title{position:absolute;left:0;width:1200px;top:92px;text-align:center;font-family:"Open Sans",sans-serif;font-weight:700;font-size:45px;color:var(--navy-deep)}
.hero-cta{position:absolute;left:435px;top:183px;width:328px;height:55px;background:var(--navy-deep);color:#fff;font-family:"Open Sans",sans-serif;font-size:14px;text-align:center;line-height:55px}
.hero-band{position:absolute;left:0;bottom:0;width:1200px;height:68px;background:rgba(40,40,40,.55)}
.hero-band h2{position:absolute;left:106px;top:14px;color:#fff;font-family:"Open Sans",sans-serif;font-weight:600;font-size:30px}
.dots{position:absolute;left:1026px;top:27px;display:flex;gap:7px;align-items:center}
.dots span{width:11px;height:11px;border-radius:50%;background:#fff}
.dots span.on{width:15px;height:15px;background:transparent;border:2px solid #fff}

/* partners */
.partners{position:absolute;left:84px;top:819px;width:1029px;height:119px;border:1px solid var(--rule);display:flex}
.partners .cell{flex:1;display:flex;align-items:center;justify-content:center;border-right:1px solid var(--rule)}
.partners .cell:last-child{border-right:none}
.arrow{position:absolute;top:868px;width:23px;height:23px;border-radius:50%;background:#8c8c8c}

/* cards */
.card{position:absolute;width:328px;height:400px;background:var(--card-body)}
.card h3{height:47px;background:var(--card-head);color:#fff;font-family:"Open Sans",sans-serif;font-weight:600;font-size:20px;line-height:47px;padding-left:16px}
.card .photo{height:178px}
.card .body{padding:16px 10px 0}
.card h4{font-family:"Arimo",sans-serif;font-style:italic;font-weight:400;font-size:14px;color:#333;margin-bottom:6px}
.card p{font-size:11.3px;line-height:21px;color:#555;margin-bottom:12px}
.card a{color:var(--link);text-decoration:none}

/* footer */
.footer-rule{position:absolute;left:0;top:1909px;width:1200px;height:1px;background:var(--rule)}
.footer h5{font-family:"Open Sans",sans-serif;font-weight:400;font-size:19px;color:#444}
.links{position:absolute;left:84px;top:1930px}
.link-cols{display:grid;grid-template-columns:169px 120px;row-gap:8px;margin-top:17px}
.link-cols a{font-size:11px;color:#777;text-decoration:none;padding-left:14px;position:relative;line-height:17.5px}
.link-cols a::before{content:"";position:absolute;left:0;top:6px;width:4px;height:4px;border-top:1px solid #999;border-right:1px solid #999;transform:rotate(45deg)}
.vrule{position:absolute;top:1941px;width:1px;height:164px;background:var(--rule)}
.contact{position:absolute;left:434px;top:1930px;width:230px}
.contact p{font-size:11px;color:#888;line-height:20px;margin-top:10px}
.contact p:first-of-type{margin-top:17px}
.seal{position:absolute;left:693px;top:1949px}
.guarantee{position:absolute;left:843px;top:1974px;width:280px}
.guarantee h6{font-family:"Open Sans",sans-serif;font-weight:400;font-size:14px;color:#333}
.guarantee p{font-size:11px;color:#999;line-height:20px;margin-top:6px}

.site-foot{position:absolute;left:0;top:2132px;width:1200px;height:74px;background:var(--navy-deep)}
.site-foot small{position:absolute;left:85px;top:30px;color:#fff;font-size:11px}
.social{position:absolute;left:917px;top:20px;display:flex;gap:9px}
.social span{width:32px;height:32px;border-radius:50%;border:1.5px solid #fff}
</style>
</head>
<body>

<header class="site-header">
  <div class="brand">
    <div class="brand-name">CORBECK</div>
    <div class="brand-sub">Aluminium Ltd</div>
    <div class="brand-place">Upper Hutt &nbsp;&nbsp;&nbsp; Wellington</div>
  </div>
  <div class="brand-square"></div>
  <div class="call">CALL US : (04)-555-0182</div>
  <div class="excellence"><span class="lead">EXCELLENCE</span><span class="rest">IN ALUMINIUM WINDOWS &amp; DOORS</span></div>
  <div class="partner-mark"><i></i>PELVANE</div>
</header>

<nav class="main-nav">
  <a>Home</a><a>About Us</a><a>Commercial</a><a>New Homes</a><a>Replacement Joinery</a><a>Double Glazing</a><a>Conservatories</a><a>Gallery</a><a>Free Quote</a><a>Contact Us</a>
</nav>

<div class="tagline">ENSURING STYLE AND FUNCTIONALITY WITH YOUR ALIMINIUM JOINERY</div>

<section class="hero">
  <div class="hero-photo" role="img" aria-label="Row of white townhouses with grey aluminium bay windows under a blue sky, hedge in front"></div>
  <h1 class="hero-title">CORBECK ALUMINIUM LTD</h1>
  <div class="hero-cta">GET A FREE QUOTE FOR YOUR JOINERY NEEDS</div>
  <div class="hero-band">
    <h2>NEW HOMES</h2>
    <div class="dots"><span></span><span class="on"></span><span></span><span></span><span></span></div>
  </div>
</section>

<div class="arrow" style="left:64px"></div>
<div class="partners">
  <div class="cell"><svg width="100" height="60"><rect x="20" y="8" width="60" height="44" fill="#e3141b"/></svg></div>
  <div class="cell"><svg width="130" height="60"><ellipse cx="65" cy="30" rx="58" ry="24" fill="#8a5a3a"/></svg></div>
  <div class="cell"><svg width="90" height="90"><circle cx="45" cy="45" r="42" fill="#1f3d5e"/></svg></div>
  <div class="cell"><svg width="140" height="30"><rect x="2" y="4" width="136" height="22" fill="none" stroke="#444" stroke-width="1.5"/></svg></div>
  <div class="cell"><svg width="80" height="80"><circle cx="40" cy="40" r="34" fill="none" stroke="#333" stroke-width="2"/></svg></div>
  <div class="cell"><svg width="150" height="30"><rect x="2" y="4" width="146" height="22" fill="#0b1c86"/></svg></div>
</div>
<div class="arrow" style="left:1109px"></div>

<article class="card" style="left:84px;top:1003px">
  <h3>NEW HOMES</h3>
  <div class="photo" role="img" aria-label="Conservatory with aluminium-framed glass walls on a new home" style="background:linear-gradient(180deg,#4b6d9a,#a7b9c8 55%,#6a5a48)"></div>
  <div class="body">
    <h4>Buliding Your Dream Home</h4>
    <p>We are all established builders and aluminium joiners, offering can talk to the business owner, not a sales person.</p>
    <p>We are all established builders and aluminium joiners, offering a personal service where you can talk to the business owner, not a sales person.<a>Click Here</a></p>
  </div>
</article>

<article class="card" style="left:437px;top:1003px">
  <h3>COMMERCIAL</h3>
  <div class="photo" role="img" aria-label="White commercial building with rows of aluminium bay windows" style="background:linear-gradient(180deg,#8fb6e0,#e6e6e2 50%,#5f7a3c)"></div>
  <div class="body">
    <h4>Improve The Presentaion Of Your Business</h4>
    <p>We are all established builders and aluminium joiners, offering can talk to the business owner, not a sales person.</p>
    <p>We are all established builders and aluminium joiners, offering a personal service where you can talk to the business owner, not a sales person.<a>Click Here</a></p>
  </div>
</article>

<article class="card" style="left:788px;top:1003px">
  <h3>REPLACEMENT JOINERY</h3>
  <div class="photo" role="img" aria-label="House with new aluminium windows and balcony railing" style="background:linear-gradient(90deg,#b9b9b4,#e2e2dc 55%,#4f6b3a)"></div>
  <div class="body">
    <h4>Tired Of Your Old Windows And Doors?</h4>
    <p>We are all established builders and aluminium joiners, offering can talk to the business owner, not a sales person.</p>
    <p>We are all established builders and aluminium joiners, offering a personal service where you can talk to the business owner, not a sales person.<a>Click Here</a></p>
  </div>
</article>

<article class="card" style="left:224px;top:1462px">
  <h3>DOUBLE GLAZING</h3>
  <div class="photo" role="img" aria-label="Modern apartment building with double glazed aluminium windows" style="background:linear-gradient(90deg,#7a8a96,#d3d7da 45%,#3a3a3a)"></div>
  <div class="body">
    <h4>Enjoy The Many Benefits Of Double Glazing</h4>
    <p>We are all established builders and aluminium joiners, offering can talk to the business owner, not a sales person.</p>
    <p>We are all established builders and aluminium joiners, offering a personal service where you can talk to the business owner, not a sales person.<a>Click Here</a></p>
  </div>
</article>

<article class="card" style="left:637px;top:1462px">
  <h3>CONSERVATORIES</h3>
  <div class="photo" role="img" aria-label="Building entrance with aluminium conservatory glazing" style="background:linear-gradient(180deg,#3c3f44,#8d9aa3 50%,#d6d2c8)"></div>
  <div class="body">
    <h4>Enjoy The SUn All Year Round!</h4>
    <p>We are all established builders and aluminium joiners, offering can talk to the business owner, not a sales person.</p>
    <p>We are all established builders and aluminium joiners, offering a personal service where you can talk to the business owner, not a sales person.<a>Click Here</a></p>
  </div>
</article>

<div class="footer-rule"></div>
<footer class="footer">
  <div class="links">
    <h5>LINKS</h5>
    <div class="link-cols">
      <a>Home</a><a>Double Glazing</a>
      <a>About Us</a><a>Conservatories</a>
      <a>Commercial</a><a>Gallery</a>
      <a>New Homes</a><a>Get a Free Quote</a>
      <a>Replacement Joinery</a><a>Contact Us</a>
    </div>
  </div>
  <div class="vrule" style="left:394px"></div>
  <div class="contact">
    <h5>CONTACT DETAILS</h5>
    <p>Phone: (04) 555 0182</p>
    <p>Fax: (04) 555 0187</p>
    <p>Physical address: 41 Harwell Cres,<br>Upper Hutt</p>
    <p>Postal address: PO Box 70315,<br>Upper Hutt</p>
  </div>
  <div class="vrule" style="left:675px"></div>
  <svg class="seal" width="134" height="134"><circle cx="67" cy="67" r="64" fill="var(--gold)"/><circle cx="67" cy="67" r="46" fill="#2a2414"/></svg>
  <div class="guarantee">
    <h6>CUSTOMER SATISFACTION GUARANTEE</h6>
    <p>We guarantee our work. If there are ever any problems, we will be back to provide a solution.</p>
  </div>
</footer>

<div class="site-foot">
  <small>© Copy Rights &nbsp;2014-Corbeck Aluminium. All Rights Reserved.</small>
  <div class="social"><span></span><span></span><span></span><span></span><span></span></div>
</div>

</body>
</html>
```